Mobile Repair Service on location needs a Web Design

We are starting a new mobile device repair service called Handset Haven and our website needs a design!

Hello Designers!
First, we'd like to make clear this is more than a simple web design contest, we want the designers to create an idea. We want someone who can create the whole theme of the service's we provide. We want someone that can help design our visual branding, help us communicate a sentiment. And we are willing to pay for that.

Who are we?
Our company is based in Rotterdam, the Netherlands. We provide different services for all kinds of electronic devices. The kind of services we provide are, among other things, installations of hardware and software and the repair of broken or malfunctioning devices.
We are starting a new service that offers mobile device repairs on location, be it at the home of our customers, their office, or any other place. Just give us the address and we will come to you for the repair job. This is also our main USP. We have multiple skilled engineers who drive trough the country on a daily basis and can be on location within a working day. Repair is done immediately onsite while the customer waits. At this stage we will start with the smartphone product-group within the mobile devices. In a second phase we might also add tablets.
People don't want to be without their phone for weeks because of some parts that needed to be ordered by a repair center they had to sent their phone to. We offer a fully functional mobile repair center in the form of specially customized vans. These vans have all the tools and utilities needed by our engineers to safely repair your mobile device. Your phone is being repaired directly in front of you, the next business-day, on a location you desire.

For this new service we are creating a website called Handset Haven. The website needs a story and matching design and this is where you come in. We are not looking for a simple template design we can get from any place. We need a story. We want you to create an idea, build a unique theme or vision that helps sell the product/service. This goes beyond the design of the website. We need the whole package, the design you are creating needs to have returning elements like icons, color use, images, maybe even characters etc. You name it! There needs to be a common thread in the design so we can reuse elements in, for example, the email templates, the work order or receipt we give to our customers (we may contact the winner of the contest to design these for us as well!).

The name 'Handset Haven' is chosen. Rehab (short for rehabilitate) has a bold and playful tone to it and the design needs to reflect the name. So we're looking for a somewhat playful and cheeky design. Definitely not too serious and definitely modern. We already got a logo that we love and that fit's this description (see attached design documents for the logo). It's bold, powerful and fun. Our web design needs to reflect this as well and has to fit in with our logo.
We would really like it if the design somehow incorporates elements that highlight our unique selling points (repairs on location, we come to you etc.). We would really like some form of story telling in the design. Think clumsy people breaking their phones. Teenagers in tears because they have no access to their friends. People nowadays have the need to always be 'connected'. What happens when your phone is broken or malfunctioning? We're handling tech, we are nerds and a little bit weird, but we're professionals and here to help you with your problem. The sentiment Byte Brigade tries to communicate is something we really like. We're looking for fresh idea's, anything goes!

In an overview all Unique Selling Points of the Handset haven service:
- Professional service on location. Don’t ship to us we will come to you!
- Clear pricing upfront. No hidden cost.
- Next business-day repair.
- Backed by a professional call center open 12 hours a day and open on a Saturday as well
- Backed by a professional repair center with more then 12 years of experience
- Repair is done by certified engineers
- 1 year warranty on the repair

The process:
The main function of our website will be for customers to make a repair request. A customer will visit our website and can make a repair request immediately by going through a 'request-order-flow'. In this flow he or she will need to fill in some forms and can select wich type/model/brand of mobile device he or she has and what parts need to be repaired. After a request is placed we will call the customer back (within an hour) for a short intake and to set a date/time and location. Our engineer will meet the customer at the specified location and will repair the device onsite in one of our mobile repair centers, which is a specialized van equipped with all the tools needed for device restorations.
So in short the steps are:
- Choose your device and repair job
- Place the order
- Get a callback within the hour
- Set date and location
- We will come to you.

Website functionality:
Our website is our main form of communication. So the sentiment we want to communicate needs be reflected in the design. We need a main/front page designed (preferably a long scrolling page design) containing:
1. Customers will be able to request a repair job directly on our website. So there will need to be a prominent button/link at the top of our main page that will bring the customer to this 'request-order-flow'. This is the main flow which needs to be full focus on the front page. All other items are secondary.
2. The general information of who we are and what we do, and why the customer should choose us. Preferably in short bullet-point type keywords/sentences with icons or other visual cues. See our unique selling points to get an idea of the information that will be displayed here.
3. There needs to be a section that will explain the process (see above) of a repair request step-by- step, again in brief short key sentences and with (custom) icons.
4. There needs to be a section that explains to the customer he/she can always contact us if they are not sure what the problem is with their device, and for this reason are not sure what repair request they should order.
5. We want to implement some functionality that display customer ratings or customer reviews. So there needs to be room for some kind of widget of plugin we're going to implement which shows these reviews.
6. A 'For business section' where we will explain all the options we provide for corporate clients.
7. Social media links.
8. There needs to be a menu with buttons that leads to the all sections described in the previous points.

For now, we need a design for our front page. In the second phase, when we have picked our winner, we may ask the winner to design the page(s) for our request workflow as well.

EDIT:
Finally, we have a very specific order in mind for the different segments of our website. We would like you to add some more segments that were not in our original brief as well:

1. Top header with order/request button. (should instantly make clear our main USP, we do repairs on location)
2. Our process
3. Our unique selling points / why choose us
4. The kind of repairs we do (broken screens, broken batteries, water damage, broken camera's, no sound etc.)
5. A 'meet our team' section, where we introduce some of our engineers
6. A 'contact us for any questions' section/
7. Testimonials/user reviews
8. A section where we show key performance indicators
9. 'For businesses' sections
10.'Subscribe for newsletter' field
11. Social media buttons

Industry/Entity Type

It Service

Number of Pages Required

1 page

Font styles to use
Sans Serif

Requirements
Must have
• a main/front page, design only
• custom icons/images for banners, adverts online and in print (high res)
Nice to have
• Storytelling in our design.
• Design that fits with our brand new logo.
• Elements like icons to have a flat design.
• Keep in mind that the website will need to be responsive when designing! (Ideally provide an example of the mobile design as well)
• Create a fun and trustworthy feeling.

```html
<!DOCTYPE html>
<html lang="en">
<head>
<meta charset="utf-8">
<title>Handset Haven – Repairs On Location</title>
<link rel="stylesheet" href="https://fonts.googleapis.com/css2?family=Roboto:wght@400;500;700;900&family=Roboto+Condensed:wght@700&display=swap">
<style>
:root{
  --orange:#f26522;
  --orange-dark:#d9531a;
  --ink:#1f1f1f;
  --text:#555;
  --muted:#888;
  --grey-bg:#ececec;
  --hero-deep:#0b2a5c;
  --hero-mid:#1d5fb5;
  --dark:#2b2b2b;
  --footer:#3b3b3b;
  --white:#fff;
}
*{box-sizing:border-box;margin:0;padding:0}
html,body{width:1200px;height:4296px;overflow:hidden}
body{font-family:"Roboto",Arial,sans-serif;color:var(--text);background:var(--white);position:relative}
section,header,footer{position:absolute;left:0;width:1200px}
.abs{position:absolute}
.btn{display:inline-block;background:var(--orange);color:var(--white);font-weight:700;text-transform:uppercase;text-align:center;font-size:14px;letter-spacing:.3px}
.section-title{font-size:34px;font-weight:700;color:var(--ink)}
.underline{width:46px;height:4px;background:var(--orange)}
p.body{font-size:12.5px;line-height:19px;color:var(--text)}
.brand{display:flex;align-items:center;gap:10px}
.brand-dot{width:34px;height:34px;border-radius:50%;background:var(--orange)}
.brand-name{font-weight:900;font-size:20px;color:var(--orange);text-transform:uppercase;line-height:1}

/* nav */
.site-nav{top:0;height:72px;background:var(--white)}
.site-nav .brand{position:absolute;left:172px;top:18px}
.menu{position:absolute;left:536px;top:28px;display:flex;gap:26px;font-size:13px;font-weight:500;color:var(--ink)}
.site-nav .btn{position:absolute;left:860px;top:16px;width:166px;height:40px;line-height:40px;font-size:13px}

/* hero */
.hero{top:72px;height:523px;background:linear-gradient(100deg,var(--hero-deep) 0%,#103d82 45%,var(--hero-mid) 75%,var(--hero-deep) 100%)}
.hero-photo{position:absolute;left:0;top:0;width:1200px;height:523px}
.hero-device{position:absolute;left:260px;top:0;width:280px;height:500px;border-radius:26px;background:linear-gradient(180deg,#2c6fd0,#13418a);opacity:.75}
.hero-copy{position:absolute;left:563px;top:128px}
.hero-title{font-family:"Roboto Condensed","Roboto",sans-serif;font-weight:700;font-size:54px;line-height:50px;color:var(--white);text-transform:uppercase}
.hero-title em{font-style:normal;color:var(--orange)}
.hero-sub{margin-top:12px;font-family:"Roboto Condensed",sans-serif;font-weight:700;font-size:27px;line-height:30px;color:var(--white);text-transform:uppercase}
.hero .btn{margin-top:26px;width:206px;height:44px;line-height:44px}
.dots{position:absolute;left:630px;top:455px;display:flex;gap:10px}
.dots span{width:11px;height:11px;border-radius:50%;background:#9fb3d3}
.dots span.on{background:var(--orange)}

/* about */
.who{top:640px;height:410px}
.photo{background:linear-gradient(135deg,#c9c4bd,#8e857a)}
.who .photo-a{left:172px;top:14px;width:372px;height:262px;border:6px solid var(--orange)}
.who .photo-b{left:288px;top:72px;width:358px;height:298px;border:6px solid var(--white);box-shadow:0 4px 14px rgba(0,0,0,.18);background:linear-gradient(135deg,#a9a097,#6e665d)}
.who .copy{left:684px;top:38px;width:344px}
.who .section-title,.what .section-title{font-size:30px}
.copy .underline{margin:12px 0 20px}
.copy p+p{margin-top:16px}
.what{top:1060px;height:290px}
.what .copy{left:172px;top:20px;width:344px}
.what .photo{left:612px;top:14px;width:420px;height:262px;background:linear-gradient(135deg,#f1f2f4 0%,#d9dde2 60%,#b9c0c8 100%)}

/* why */
.why{top:1350px;height:805px;background:var(--grey-bg)}
.why .section-title{position:absolute;top:52px;width:100%;text-align:center}
.why-map{position:absolute;left:250px;top:330px;width:700px;height:420px;background:linear-gradient(180deg,rgba(220,220,220,0) 0%,#dedede 40%,#d8d8d8 100%)}
.usp{position:absolute;font-size:13px;line-height:1.45;color:var(--ink);width:190px}
.usp.left{text-align:right}
.why svg{position:absolute;left:0;top:0}

/* process */
.process{top:2155px;height:695px}
.process .section-title{position:absolute;top:60px;width:100%;text-align:center}
.request-form{position:absolute;left:321px;top:285px;width:324px}
.request-form h3{color:var(--white);font-size:30px;font-weight:700;text-align:center;margin-bottom:14px}
.field{background:var(--white);height:30px;font-size:12px;color:var(--muted);line-height:30px;padding:0 10px;border-radius:2px}
.row{display:flex;gap:14px;margin-top:12px}
.row .field{flex:1;position:relative}
.row .field:after{content:"";position:absolute;right:10px;top:12px;border:5px solid transparent;border-top-color:#666}
.radios{display:flex;justify-content:center;gap:20px;margin-top:12px;color:var(--white);font-size:12px}
.radios span:before{content:"";display:inline-block;width:10px;height:10px;border-radius:50%;background:var(--white);margin-right:5px;vertical-align:-1px}
.request-form .submit{display:block;margin:14px auto 0;width:200px;height:40px;line-height:40px;background:#111;color:var(--white);font-weight:700;font-size:14px;text-align:center}
.step-label{position:absolute;font-size:14px;color:var(--ink)}
.process svg{position:absolute;left:0;top:0}

/* reviews */
.reviews{top:2850px;height:587px;background:var(--dark);overflow:hidden}
.reviews-bg{position:absolute;inset:0;background:linear-gradient(180deg,#3a3a3a,#222)}
.reviews .quote{position:absolute;top:40px;width:100%;text-align:center;font-size:60px;font-weight:900;color:var(--white);line-height:1}
.reviews .section-title{position:absolute;top:84px;width:100%;text-align:center;color:var(--white)}
.card{position:absolute;top:170px;width:262px;height:226px;background:var(--white);text-align:center;padding:18px 18px}
.card p{font-size:11px;line-height:1.5;color:var(--muted);font-style:italic}
.stars{color:var(--orange);font-size:16px;letter-spacing:2px;margin-top:8px;line-height:20px}
.card b{display:block;font-size:13px;color:var(--ink);margin-top:2px}
.card small{font-size:11px;color:var(--muted)}
.card:after{content:"";position:absolute;left:50%;bottom:-14px;margin-left:-14px;border:14px solid transparent;border-bottom:0;border-top-color:var(--white)}
.avatar{position:absolute;top:428px;width:68px;height:68px;border-radius:50%;border:4px solid var(--white);background:linear-gradient(135deg,#c9a88e,#7d5e4b)}

/* corporate */
.corporate{top:3437px;height:573px}
.corporate .section-title{position:absolute;top:48px;width:100%;text-align:center}
.corp{position:absolute;top:128px;width:270px}
.corp .photo{height:186px}
.corp h4{font-size:16px;line-height:1.3;color:var(--ink);margin-top:14px}
.corp p{font-size:11.5px;line-height:1.55;color:var(--muted);margin-top:12px}
.corp .btn{margin-top:14px;width:74px;height:26px;line-height:26px;font-size:11px;text-transform:none;font-weight:500}

/* footer */
.site-footer{top:4010px;height:286px;background:var(--footer);color:#cfcfcf}
.to-top{position:absolute;left:560px;top:-22px;width:80px;height:22px;background:var(--footer);border-radius:40px 40px 0 0}
.to-top:after{content:"";position:absolute;left:33px;top:8px;border:7px solid transparent;border-top:0;border-bottom-color:#ddd}
.site-footer .brand{position:absolute;left:172px;top:58px}
.site-footer .brand-name{color:var(--white);font-size:22px}
.site-footer .btn{position:absolute;left:172px;top:178px;width:172px;height:38px;line-height:38px;font-size:12px}
.copyright{position:absolute;left:172px;top:238px;font-size:11px}
.fcol{position:absolute;top:58px;font-size:12px;line-height:1.75}
.fcol h5{font-size:12px;color:var(--white);font-weight:700;margin-bottom:6px;text-transform:uppercase}
.fcol .phone{font-size:17px;color:var(--white);font-weight:700}
.news-form{display:flex;margin-top:8px}
.news-form .input{width:190px;height:28px;background:var(--white);color:var(--muted);font-size:11px;line-height:28px;padding:0 8px}
.news-form .go{width:80px;height:28px;background:var(--orange);color:var(--white);font-size:10px;font-weight:700;line-height:28px;text-align:center}
.socials{display:flex;gap:10px;margin-top:8px}
.socials span{width:22px;height:22px;border-radius:50%;border:2px solid #aaa}
</style>
</head>
<body>

<header class="site-nav">
  <div class="brand"><span class="brand-dot"></span><span class="brand-name">Handset Haven</span></div>
  <nav class="menu"><span>HOME</span><span>ABOUT US</span><span>SERVICES</span><span>CONTACT US</span></nav>
  <span class="btn">Request Order Flow</span>
</header>

<section class="hero">
  <div class="hero-photo" role="img" aria-label="Night city view seen through a smartphone showing a repair van"></div>
  <div class="hero-device" role="img" aria-label="Smartphone screen with service van"></div>
  <div class="hero-copy">
    <h1 class="hero-title">Professional<br>Service<br><em>On Location.</em></h1>
    <p class="hero-sub">Don't ship to us we will<br>come to you!</p>
    <span class="btn">Request Order Flow</span>
  </div>
  <div class="dots"><span class="on"></span><span></span><span></span><span></span><span></span></div>
</section>

<section class="who">
  <div class="abs photo photo-a" role="img" aria-label="Technician repairing a smartphone circuit board"></div>
  <div class="abs photo photo-b" role="img" aria-label="Hands with tools opening a phone"></div>
  <div class="abs copy">
    <h2 class="section-title">Who We Are</h2>
    <div class="underline"></div>
    <p class="body">Lorem ipsum dolor sit amet, consectetur adipiscing elit, sed do eiusmod tempor incididunt ut labore et dolore magna aliqua. Ut enim ad minim veniam, quis nostrud exercitation ullamco laboris nisi ut aliquip ex ea commodo consequat. Duis aute irure dolor in reprehenderit in voluptate velit esse cillum dolore eu fugiat nulla pariatur. Excepteur sint occaecat cupidatat non proident, sunt in culpa qui officia deserunt mollit anim id est laborum.</p>
    <p class="body">Lorem ipsum dolor sit amet, consectetur adipiscing elit, sed do eiusmod tempor incididunt ut labore et dolore magna aliqua. Ut enim ad minim veniam, quis nostrud exercitation ullamco laboris nisi ut aliquip ex ea commodo consequat.</p>
  </div>
</section>

<section class="what">
  <div class="abs copy">
    <h2 class="section-title">What We Do</h2>
    <div class="underline"></div>
    <p class="body">Lorem ipsum dolor sit amet, consectetur adipiscing elit, sed do eiusmod tempor incididunt ut labore et dolore magna aliqua. Ut enim ad minim veniam, quis nostrud exercitation ullamco laboris nisi ut aliquip ex ea commodo consequat. Duis aute irure dolor in reprehenderit in voluptate velit esse cillum dolore eu fugiat nulla pariatur. Excepteur sint occaecat cupidatat non proident, sunt in culpa qui officia deserunt mollit anim id est laborum.</p>
  </div>
  <div class="abs photo" role="img" aria-label="Engineer standing in front of the white service van"></div>
</section>

<section class="why">
  <h2 class="section-title">Why The Customer Should Choose Us</h2>
  <div class="why-map" role="img" aria-label="Isometric street map with the service van driving to the customer"></div>
  <svg width="1200" height="805" viewBox="0 0 1200 805" aria-hidden="true">
    <circle cx="601" cy="385" r="175" fill="none" stroke="#f26522" stroke-width="3"/>
    <circle cx="601" cy="385" r="62" fill="#f26522"/>
    <g fill="#fff" stroke="#f26522" stroke-width="3">
      <circle cx="601" cy="211" r="28"/>
      <circle cx="467" cy="282" r="28"/>
      <circle cx="736" cy="282" r="28"/>
      <circle cx="430" cy="388" r="28"/>
      <circle cx="773" cy="383" r="28"/>
      <circle cx="458" cy="506" r="28"/>
      <circle cx="716" cy="512" r="28"/>
    </g>
    <g fill="none" stroke="#333" stroke-width="2" stroke-linecap="round" stroke-linejoin="round">
      <path d="M601 199c-6 0-10 4-10 10 0 8 10 16 10 16s10-8 10-16c0-6-4-10-10-10z"/><circle cx="601" cy="209" r="3"/>
      <rect x="455" y="273" width="24" height="18" rx="2"/><path d="M459 280h8"/>
      <path d="M724 288v-6a12 12 0 0124 0v6"/><rect x="721" y="285" width="6" height="9" rx="2"/><rect x="745" y="285" width="6" height="9" rx="2"/>
      <rect x="416" y="380" width="20" height="14"/><path d="M436 384h8l4 5v5h-12"/><circle cx="422" cy="396" r="2"/><circle cx="442" cy="396" r="2"/>
      <path d="M763 372h20M763 394h20M765 372c0 8 16 14 16 22M781 372c0 8-16 14-16 22"/>
      <circle cx="458" cy="500" r="8"/><path d="M446 518c2-7 22-7 24 0"/>
      <path d="M716 500l10 4v7c0 7-5 11-10 13-5-2-10-6-10-13v-7z"/><path d="M711 512l4 4 6-7"/>
    </g>
    <text x="601" y="391" fill="#fff" font-family="Roboto, sans-serif" font-size="11" font-weight="900" text-anchor="middle">HANDSET HAVEN</text>
  </svg>
  <p class="usp" style="left:501px;top:126px;width:200px;text-align:center">Professional service on location. Don't ship to us we will come to you!</p>
  <p class="usp left" style="left:231px;top:255px">Clear pricing upfront.<br>No hidden cost.</p>
  <p class="usp" style="left:782px;top:242px;width:200px">Backed by a professional call center open 12 hours a day and open on a Saturday as well.</p>
  <p class="usp left" style="left:208px;top:376px">Next business-day repair.</p>
  <p class="usp" style="left:820px;top:362px;width:200px">Backed by a professional repair center with more then 12 years of experience</p>
  <p class="usp left" style="left:231px;top:490px;width:185px">Repair is done by certified engineers</p>
  <p class="usp" style="left:760px;top:500px;width:160px">1 year warranty on the repair</p>
</section>

<section class="process">
  <h2 class="section-title">The Process</h2>
  <svg width="1200" height="695" viewBox="0 0 1200 695" aria-hidden="true">
    <path d="M593 188a220 220 0 0 1 3 402" fill="none" stroke="#bbb" stroke-width="2"/>
    <circle cx="481" cy="365" r="214" fill="#f26522"/>
    <g fill="#fff" stroke="#333" stroke-width="2">
      <circle cx="593" cy="188" r="26"/>
      <circle cx="679" cy="274" r="26"/>
      <circle cx="710" cy="388" r="26"/>
      <circle cx="682" cy="503" r="26"/>
      <circle cx="596" cy="589" r="26"/>
    </g>
    <g fill="none" stroke="#333" stroke-width="2" stroke-linecap="round" stroke-linejoin="round">
      <rect x="585" y="175" width="16" height="26" rx="3"/><path d="M591 196h4"/>
      <path d="M667 266h4l4 14h14l3-10h-19"/><circle cx="677" cy="285" r="2"/><circle cx="688" cy="285" r="2"/>
      <path d="M701 381c2-4 6-4 8 0l-2 4c2 4 4 6 8 8l4-2c4 2 4 6 0 8-8 4-22-10-18-18z"/>
      <rect x="670" y="494" width="24" height="20" rx="2"/><path d="M670 500h24M676 490v6M688 490v6"/>
      <rect x="584" y="582" width="16" height="12"/><path d="M600 585h6l3 4v5h-9"/><circle cx="588" cy="596" r="2"/><circle cx="603" cy="596" r="2"/>
    </g>
    <path d="M318 520c20 40 60 60 100 50" fill="none" stroke="#111" stroke-width="4"/>
    <path d="M408 558l16 10-16 10z" fill="#111"/>
  </svg>
  <span class="step-label" style="left:656px;top:180px">Choose your device and repair job</span>
  <span class="step-label" style="left:740px;top:266px">Place the order</span>
  <span class="step-label" style="left:770px;top:380px">Get a callback within the hour</span>
  <span class="step-label" style="left:740px;top:495px">Set date and location</span>
  <span class="step-label" style="left:656px;top:582px">We will come to you.</span>
  <div class="request-form">
    <h3>A Repair Request</h3>
    <div class="field">What parts need to be repaired</div>
    <div class="row"><div class="field">Model</div><div class="field">Model</div></div>
    <div class="radios"><span>Lite</span><span>Lite</span></div>
    <span class="submit">PLACE THE ORDER</span>
  </div>
</section>

<section class="reviews">
  <div class="reviews-bg" role="img" aria-label="Darkened collage of smiling customers"></div>
  <svg class="abs" style="left:0;top:0" width="1200" height="587" viewBox="0 0 1200 587" aria-hidden="true">
    <path d="M760 0H1200V34z" fill="#f26522"/>
    <path d="M0 548L440 587H0z" fill="#f26522"/>
  </svg>
  <div class="quote">&ldquo;</div>
  <h2 class="section-title">What Our Customers Say</h2>
  <div class="card" style="left:172px"><p>Lorem ipsum dolor sit amet, consectetur adipiscing elit, sed do eiusmod tempor incididunt ut labore et dolore magna aliqua. Ut enim ad minim veniam, quis nostrud exercitation ullamco laboris nisi ut aliquip ex ea commodo consequat. Duis aute irure dolor in reprehenderit.</p><div class="stars">★★★★★</div><b>Alex Meyer</b><small>Lorem ipsum dolor</small></div>
  <div class="card" style="left:467px"><p>Lorem ipsum dolor sit amet, consectetur adipiscing elit, sed do eiusmod tempor incididunt ut labore et dolore magna aliqua. Ut enim ad minim veniam, quis nostrud exercitation ullamco laboris nisi ut aliquip ex ea commodo consequat. Duis aute irure dolor in reprehenderit.</p><div class="stars">★★★★★</div><b>Alex Meyer</b><small>Lorem ipsum dolor</small></div>
  <div class="card" style="left:762px"><p>Lorem ipsum dolor sit amet, consectetur adipiscing elit, sed do eiusmod tempor incididunt ut labore et dolore magna aliqua. Ut enim ad minim veniam, quis nostrud exercitation ullamco laboris nisi ut aliquip ex ea commodo consequat. Duis aute irure dolor in reprehenderit.</p><div class="stars">★★★★★</div><b>Alex Meyer</b><small>Lorem ipsum dolor</small></div>
  <div class="avatar" style="left:269px" role="img" aria-label="Customer portrait"></div>
  <div class="avatar" style="left:564px" role="img" aria-label="Customer portrait"></div>
  <div class="avatar" style="left:859px" role="img" aria-label="Customer portrait"></div>
</section>

<section class="corporate">
  <h2 class="section-title">We Provide For Corporate Clients</h2>
  <div class="corp" style="left:172px">
    <div class="photo" role="img" aria-label="Business team meeting around a laptop" style="background:linear-gradient(135deg,#3b4656,#1c2330)"></div>
    <h4>Lorem ipsum dolor sit amet, consectetur adipiscing elit,</h4>
    <p>Sed ut perspiciatis unde omnis iste natus error sit voluptatem accusantium doloremque laudantium, totam rem aperiam, eaque ipsa quae ab illo inventore veritatis.</p>
    <span class="btn">Read More</span>
  </div>
  <div class="corp" style="left:464px">
    <div class="photo" role="img" aria-label="Call center agent with headset" style="background:linear-gradient(135deg,#d9d2c8,#8a7a6c)"></div>
    <h4>Lorem ipsum dolor sit amet, consectetur adipiscing elit,</h4>
    <p>Sed ut perspiciatis unde omnis iste natus error sit voluptatem accusantium doloremque laudantium, totam rem aperiam, eaque ipsa quae ab illo inventore veritatis.</p>
    <span class="btn">Read More</span>
  </div>
  <div class="corp" style="left:756px">
    <div class="photo" role="img" aria-label="Hand touching a glowing network of gears" style="background:linear-gradient(135deg,#7fc4cf,#1f5f74)"></div>
    <h4>Lorem ipsum dolor sit amet, consectetur adipiscing elit,</h4>
    <p>Sed ut perspiciatis unde omnis iste natus error sit voluptatem accusantium doloremque laudantium, totam rem aperiam, eaque ipsa quae ab illo inventore veritatis.</p>
    <span class="btn">Read More</span>
  </div>
</section>

<footer class="site-footer">
  <span class="to-top"></span>
  <div class="brand"><span class="brand-dot"></span><span class="brand-name">Handset Haven</span></div>
  <span class="btn">Request Order Flow</span>
  <span class="copyright">© 2017 Handset Haven.</span>
  <div class="fcol" style="left:424px"><h5>Quick Links</h5>Home<br>About Us<br>Services<br>Contact Us</div>
  <div class="fcol" style="left:564px"><h5>Contact Us</h5>Handset Haven<br>Lorem ipsum dolor<br>City<br><br>Phone<br><span class="phone">(100) 555-010</span><br><br>Email<br>info@handsethaven.example</div>
  <div class="fcol" style="left:756px"><h5>Newsletter Subscribe</h5>Enter your email address below and get<br>the latest!
    <div class="news-form"><span class="input">Enter your Email Id here...</span><span class="go">SUBSCRIBE</span></div>
    <h5 style="margin-top:24px">Get Connect With Us</h5>
    <div class="socials"><span></span><span></span><span></span><span></span><span></span></div>
  </div>
</footer>

</body>
</html>
```